strength and conditioning business focused on helping people move more efficiently

I need a business card designed for a Philadelphia based company called Brsk Lft Motion (pronounced Brisk Lift). We offer fitness professional services with the idea of helping people feel better and move optimally. We do this by designing and walking through individualized programs as well as minor soft tissue work. Our perfect client would be athletes but we will be marketing to parents who have children that are active They remember their former athletic days and want to get as close as possible back to that feeling. Attached will be the official logo and logo formats. I would love for the design to communicate trustworthy and creative. I would also love for the design to be square with rounded edges.

Target Market(s)

Parents of athletic children
former athletes
athletes

Industry/Entity Type

Fitness

Contact Information for Business Card

Business: Brsk Lft Performance
Name: Coach Calvin Ashworth
Position: Strength and Conditioning Coach / Certified Personal Trainer
Contact: coach.ash@brsklft.com
Text: (555)204-7781

Font styles to use
Serif
Sans Serif

Colors
fbee38
fbee3e
0255a3
3176b5
ffffff

Requirements
Must have
• use of logo
Nice to have
• Square design
rounded edges

```html
<!DOCTYPE html>
<html lang="en">
<head>
<meta charset="utf-8">
<title>Brsk Lft Motion – Business Card</title>
<link rel="stylesheet" href="https://fonts.googleapis.com/css2?family=Arimo:wght@400;700&display=swap">
<style>
  :root {
    --navy: #0b2a6f;
    --navy-deep: #08235f;
    --gold: #f4c20d;
    --paper: #f6f6f4;
    --white: #ffffff;
    --backdrop: #dcdcdc;
  }
  * { margin: 0; padding: 0; box-sizing: border-box; }
  html, body {
    width: 1200px; height: 908px; overflow: hidden;
    background: var(--backdrop);
    font-family: "Arimo", Arial, sans-serif;
  }
  .canvas {
    position: relative; width: 1200px; height: 908px;
    display: flex; align-items: center; justify-content: center; gap: 60px;
  }
  .card {
    position: relative; width: 460px; height: 460px;
    border-radius: 52px; overflow: hidden;
    box-shadow: 0 10px 24px rgba(0,0,0,0.18);
  }

  /* Back side */
  .card--back { background: var(--navy); }
  .card__pattern {
    position: absolute; inset: 0;
    background: radial-gradient(circle at 50% 50%, var(--navy) 0%, var(--navy-deep) 100%);
  }
  .brand {
    position: absolute; display: flex; align-items: center; gap: 12px;
    font-weight: 700; white-space: nowrap;
  }
  .brand__dot {
    width: 22px; height: 22px; border-radius: 50%;
    border: 3px solid var(--gold);
  }
  .card--back .brand {
    left: 50%; top: 50%; transform: translate(-50%, -50%);
    color: var(--white); font-size: 34px;
  }

  /* Front side */
  .card--front { background: var(--navy); }
  .front__top {
    position: absolute; left: 0; top: 0; width: 100%; height: 168px;
    background: var(--paper);
    border-bottom: 5px solid var(--gold);
  }
  .card--front .brand {
    left: 50%; top: 84px; transform: translate(-50%, -50%);
    color: var(--navy); font-size: 40px;
  }
  .card--front .brand__dot { width: 26px; height: 26px; }
  .front__details {
    position: absolute; left: 0; right: 0; top: 196px;
    text-align: center; color: var(--white);
  }
  .coach-name {
    color: var(--gold); font-weight: 700; font-size: 25px;
    letter-spacing: 0.5px; text-transform: uppercase;
  }
  .coach-role { margin-top: 8px; font-size: 16px; line-height: 1.3; }
  .contact-divider {
    margin: 16px auto 12px; display: flex; align-items: center;
    justify-content: center; gap: 8px;
  }
  .contact-divider__line { width: 46px; height: 2px; background: var(--gold); }
  .contact-list { font-size: 17px; line-height: 1.35; list-style: none; }
</style>
</head>
<body>
<main class="canvas">
  <section class="card card--back" aria-label="Card back">
    <div class="card__pattern" role="img" aria-label="Faint repeating brand-mark pattern on navy"></div>
    <div class="brand"><span class="brand__dot"></span>Brsk Lft Motion</div>
  </section>

  <section class="card card--front" aria-label="Card front">
    <div class="front__top">
      <div class="brand"><span class="brand__dot"></span>Brsk Lft Motion</div>
    </div>
    <div class="front__details">
      <h1 class="coach-name">Coach Calvin Ashworth</h1>
      <p class="coach-role">Strength and Conditioning Coach /<br>Certified Personal Trainer</p>
      <div class="contact-divider">
        <span class="contact-divider__line"></span>
        <svg width="70" height="16" viewBox="0 0 70 16" aria-hidden="true">
          <path d="M3 4c1-2 3-2 4 0l1 2c0 1-1 2-1 2 1 2 2 3 4 4 0 0 1-1 2-1l2 1c2 1 2 3 0 4-3 2-13-8-12-12z" fill="var(--gold)"/>
          <line x1="19" y1="8" x2="24" y2="8" stroke="var(--gold)" stroke-width="2"/>
          <rect x="27" y="3" width="15" height="10" fill="var(--gold)"/>
          <path d="M27 3l7.5 6 7.5-6" fill="none" stroke="var(--navy)" stroke-width="1.5"/>
          <line x1="45" y1="8" x2="50" y2="8" stroke="var(--gold)" stroke-width="2"/>
          <circle cx="60" cy="8" r="6.5" fill="var(--gold)"/>
          <path d="M53.5 8h13M60 1.5c-3 3-3 10 0 13M60 1.5c3 3 3 10 0 13" fill="none" stroke="var(--navy)" stroke-width="1"/>
        </svg>
        <span class="contact-divider__line"></span>
      </div>
      <ul class="contact-list">
        <li>(555)204-7781</li>
        <li>coach.ash@brsklft.com</li>
        <li>www.brsklft.com</li>
      </ul>
    </div>
  </section>
</main>
</body>
</html>
```